Marisole Hair Flyer - tri-fold

I have added 2 participation payments to the project. I am not sure how I allocate them, but I would like to award them to two particular designers. When I find out how to do it I will allocate them. Thank you to everyone that participated, most designs were outstanding, and it was very hard to chose a winner.
========================================
PLEASE NO NEW DESIGNERS. I HAVE ENOUGH GOOD DESIGNS NOW, THAT I WILL WORK WITH ON THE EXISTING DESIGNERS. THANK YOU FOR ALL PARTICIPATING. THE QUALITY OF ALL SUBMISSIONS HAS EXCEEDED MY EXPECTATIONS, AND IS MAKING THE CHOICE DIFFICULT.
==============================================================

I have attached a proof pdf which is my draft design (I just used a stock template from Printwell) to do the mock up.

I would like you to replace the 3 main pictures of models with those I have attached. The name of the files will tell you where they should go.
I have attached pictures of all the stock photos as well, and most of the text is in the text file to save you typing it in.

I want the background colour to match Marisole colours so black with a fade to gold or something like that, must look sophisticated. I have attached Marisole logo files in black and white background.

The main pictures I have attached from the models will need to be blended into the background as well, but the hair still needs to be visible (might be hard given it is black hair as well,). The title stripes should be a gold fade as well, and the marisole text should be replaced with our logo.

please also add in the plain circle and Chat logo's in the appropriate places. The dimensions should be 279mm * 216mm and print in the PrintWell tri-fold brochure.

Possible ongoing work for the winning person, as the original designer of the logo only does logos/business cards, not other print material. Have logos in other formats (ai/cdr/jpeg) if required

Target Market(s)

African women

Industry/Entity Type

Hair

Font styles to use
Serif

Requirements
Must have
• Logo, product pictures, attached text, layout changes to draft mock up is ok if it looks better. Must conform to Printwell tri-fold layout
Nice to have
• Based on logo colours, black, white, gold complimentary colours to that palette are ok

```html
<!DOCTYPE html>
<html lang="en">
<head>
<meta charset="utf-8">
<title>Marisole Hair Tri-fold Flyer</title>
<link href="https://fonts.googleapis.com/css2?family=Tinos:wght@400;700&display=swap" rel="stylesheet">
<style>
:root{
  --stage:#2f2f2f;
  --paper:#ffffff;
  --gold:#c9a227;
  --gold-dark:#a9861c;
  --ink:#111111;
  --text:#222222;
  --band:#1c1b17;
}
*{margin:0;padding:0;box-sizing:border-box}
html,body{width:1200px;height:1200px;overflow:hidden;background:var(--stage);font-family:"Tinos",serif;color:var(--text)}
.brochure{position:absolute;left:110px;top:197px;width:982px;height:760px;background:var(--paper);overflow:hidden;box-shadow:0 10px 30px rgba(0,0,0,.5)}
.panel{position:absolute;top:0;height:760px}
.panel--left{left:0;width:327px;background:linear-gradient(180deg,#f3f3f3,#ffffff 60%)}
.panel--middle{left:327px;width:328px;background:linear-gradient(90deg,#e6e6e6,#f5f5f5 60%,#ececec)}
.panel--right{left:655px;width:327px;background:linear-gradient(180deg,#ffffff,#ebebeb)}
.title-tab{position:absolute;top:41px;height:33px;border-radius:6px;background:linear-gradient(180deg,#d4b03a,var(--gold-dark));color:#fff;font-size:20px;font-weight:400;text-align:center;line-height:33px;letter-spacing:.3px}
.title-tab--testimonials{left:24px;width:280px}
.title-tab--about{left:399px;width:183px}
.quote{position:absolute;left:46px;width:236px;font-size:12px;line-height:13.6px;text-align:center;color:var(--ink)}
.quote .mark{color:var(--gold);font-size:26px;font-weight:700;line-height:0;vertical-align:-9px}
.quote-author{display:block;font-size:15px;margin-top:10px}
.quote--first{top:100px}
.quote--second{top:233px}
.divider{position:absolute;left:60px;top:208px;width:208px;border:0;border-top:1px solid #777}
.photo{position:absolute}
.photo--straight{left:0;top:372px;width:327px;height:388px;background:radial-gradient(ellipse at 55% 45%,#3a3a3a 0%,#151515 45%,rgba(255,255,255,0) 72%)}
.photo--curly{left:590px;top:150px;width:392px;height:520px;background:radial-gradient(ellipse at 55% 45%,#9a7657 0%,#5a4030 40%,rgba(240,240,240,0) 72%)}
.about{position:absolute;left:348px;top:100px;width:284px;font-size:12px;line-height:13.6px;text-align:center;color:var(--ink)}
.about p{margin-bottom:6px}
.call-title{position:absolute;left:327px;top:306px;width:328px;text-align:center;font-size:22px;font-weight:700;color:var(--ink)}
.call-text{position:absolute;left:370px;top:342px;width:242px;text-align:center;font-size:15px;line-height:17.5px;color:#333}
.contact{position:absolute;top:421px;font-size:12.5px;color:#333}
.contact strong{display:block;font-size:14px;letter-spacing:.5px;color:var(--ink)}
.contact .phone{display:flex;align-items:center;gap:5px;margin-top:12px;font-size:14px}
.contact--a{left:357px}
.contact--b{left:507px}
.contact-divider{position:absolute;left:485px;top:421px;height:72px;border-left:1px solid #555}
.chat-dot{position:absolute;left:475px;top:515px;width:32px;height:32px;border-radius:50%;background:var(--ink)}
.chat-text{position:absolute;left:327px;top:558px;width:328px;text-align:center;font-size:15.5px;color:var(--ink)}
.brand{position:absolute;left:655px;top:16px;width:327px;text-align:center;color:var(--ink)}
.brand-dot{width:58px;height:58px;border-radius:50%;background:var(--gold);margin:0 auto 20px}
.brand-name{font-size:36px;letter-spacing:1.5px;line-height:1}
.brand-tagline{font-size:14px;margin-top:4px}
.band{position:absolute;left:327px;top:620px;width:655px;height:140px}
.follow{position:absolute;left:428px;top:686px;color:#fff;font-size:22px}
.social{position:absolute;left:430px;top:720px;display:flex;align-items:center;gap:6px;color:#fff;font-size:14px}
.social-dot{width:16px;height:16px;border-radius:50%;background:var(--gold)}
.site{position:absolute;left:712px;top:718px;color:#fff;font-size:14px}
</style>
</head>
<body>
<main class="brochure">
  <section class="panel panel--left"></section>
  <section class="panel panel--middle"></section>
  <section class="panel panel--right"></section>

  <div class="photo photo--straight" role="img" aria-label="Photo of a model with long straight black hair"></div>
  <div class="photo photo--curly" role="img" aria-label="Photo of a smiling model with voluminous curly hair"></div>

  <h2 class="title-tab title-tab--testimonials">CUSTOMER TESTIMONIALS</h2>
  <blockquote class="quote quote--first"><span class="mark">&ldquo;</span>I went to buy 20in straight but ended up buying 22in*2, 16in n 14in ..... I still didn't leave without picking 12in n 14in of the lovely curly beauty. Super human hair I must confess. The difference is overly clear.<span class="mark">&rdquo;</span>
    <span class="quote-author">Adaeze Morgan (Abuja)</span></blockquote>
  <hr class="divider">
  <blockquote class="quote quote--second"><span class="mark">&ldquo;</span>Just thought I'd let you know. I used your hair today and it is the best hair I have ever used. Could I get 3 pieces of the 18in Curly for my daughters Wedding.<span class="mark">&rdquo;</span>
    <span class="quote-author">Renata (Hurstville, Australia)</span></blockquote>

  <h2 class="title-tab title-tab--about">ABOUT US</h2>
  <div class="about">
    <p>We are an Australian based hair wholesaler that sources the best quality hair in bulk from around the world.</p>
    <p>We sell predominately through Salons in Australia, Nigeria , South Africa and Ghana. We build mutually beneficial relationships with our Salons, and consistently offer the best quality at the lowest possible price.</p>
    <p>Our consignment model, allows Salons to provide top quality hair, without having to purchase the hair upfront.</p>
    <p>Talk to our agent about our unique consignment model for selected Salons, and see whether you are elegible.</p>
  </div>
  <h3 class="call-title">Call us today!</h3>
  <p class="call-text">If you are interested in becoming a Marisole Hair stockist. Ask about our marketing support.</p>
  <div class="contact contact--a"><strong>CHIOMA</strong>Manager, Nigeria
    <span class="phone"><svg width="13" height="13" viewBox="0 0 24 24"><circle cx="12" cy="12" r="11" fill="none" stroke="#222" stroke-width="2"/><path d="M8 6l2 0 1 3-1.5 1.2a8 8 0 0 0 4.3 4.3L15 13l3 1v2c0 1-1 2-2 2A10 10 0 0 1 6 8c0-1 1-2 2-2z" fill="#222"/></svg>0703 555 0182</span></div>
  <div class="contact-divider"></div>
  <div class="contact contact--b"><strong>LINDIWE</strong>African Sales Manager
    <span class="phone"><svg width="13" height="13" viewBox="0 0 24 24"><circle cx="12" cy="12" r="11" fill="none" stroke="#222" stroke-width="2"/><path d="M8 6l2 0 1 3-1.5 1.2a8 8 0 0 0 4.3 4.3L15 13l3 1v2c0 1-1 2-2 2A10 10 0 0 1 6 8c0-1 1-2 2-2z" fill="#222"/></svg>+ 61 400 555 217</span></div>
  <div class="chat-dot"></div>
  <p class="chat-text">contact either on Chat</p>

  <div class="brand">
    <div class="brand-dot"></div>
    <div class="brand-name">MARISOLE</div>
    <div class="brand-tagline">100% Human Hair</div>
  </div>

  <svg class="band" viewBox="0 0 655 140" preserveAspectRatio="none" aria-hidden="true">
    <path d="M0 140 C40 60 120 10 260 14 C420 18 520 40 655 30 L655 140 Z" fill="var(--gold)"/>
    <path d="M4 140 C50 70 130 24 270 30 C420 36 520 58 655 42 L655 140 Z" fill="var(--band)"/>
  </svg>
  <p class="follow">Follow us on</p>
  <p class="social"><span class="social-dot"></span>/Marisolehairng</p>
  <p class="site">www.marisolehair-store.com</p>
</main>
</body>
</html>
```